Homemaking training schools needs a Business Card design

Designer, Hello!

No special requirements, good-looking enough.
--------------------------------------------------------------------------

Name: Marcus Dole
Chairman
Tel: 0574-71948263
Mobile: 13857420916
Email: kelvora@mailnest.example
Web: www.prt2019.example
Add: No.258, LanpingJie, BeiyuanQu, Ningbo, Zhejiang

LOGO
Ningbo PRT Homemaking Training School

Target Market(s)

pregnant women, mothers, infants, the elderly and families, including cleaning, cooking, nursing training.

Industry/Entity Type

Business

Contact Information for Business Card

Name: Marcus Dole
Chairman
Tel: 0574-71948263
Mobile: 13857420916
Email: kelvora@mailnest.example
Web: www.prt2019.example

LOGO

Font styles to use
Serif
Sans Serif
Decorative

Requirements
Nice to have
• Feels: clean, specifications, safety, comfort, warmth and happiness.

```html
<!DOCTYPE html>
<html lang="en">
<head>
<meta charset="utf-8">
<title>PingRuiTang Business Card</title>
<link rel="stylesheet" href="https://fonts.googleapis.com/css2?family=Arimo:wght@400;700&display=swap">
<style>
  :root {
    --stage: #2a2a2a;
    --card: #ffffff;
    --card-shade: #eeeeee;
    --brand-blue: #1b6cb5;
    --brand-pink: #e0138c;
    --on-blue: #ffffff;
  }
  html, body {
    margin: 0;
    width: 1200px;
    height: 997px;
    overflow: hidden;
    background: var(--stage);
  }
  .stage {
    position: relative;
    width: 1200px;
    height: 997px;
  }
  .card {
    position: absolute;
    left: 250px;
    width: 700px;
    height: 420px;
    border-radius: 24px;
    overflow: hidden;
    background: linear-gradient(160deg, var(--card) 55%, var(--card-shade));
  }
  .card--contact { top: 52px; }
  .card--brand { top: 525px; }
  .card svg.bands {
    position: absolute;
    inset: 0;
  }
  .band-blue { fill: var(--brand-blue); }
  .band-pink { fill: var(--brand-pink); }

  .company-name {
    position: absolute;
    margin: 0;
    font-family: "Arimo", sans-serif;
    font-weight: 700;
    color: var(--brand-blue);
    line-height: 1;
    white-space: nowrap;
  }
  .card--contact .company-name {
    top: 70px;
    right: 56px;
    font-size: 32px;
  }
  .card--brand .company-name {
    top: 160px;
    left: 0;
    width: 700px;
    text-align: center;
    font-size: 50px;
  }

  .person {
    position: absolute;
    left: 48px;
    top: 186px;
    font-family: "Arimo", sans-serif;
  }
  .person__name {
    margin: 0;
    font-size: 26px;
    font-weight: 700;
    color: var(--brand-blue);
  }
  .person__title {
    margin: 2px 0 0;
    font-size: 15px;
    color: var(--brand-pink);
  }
  .contacts {
    position: absolute;
    left: 44px;
    top: 300px;
    margin: 0;
    padding: 0;
    list-style: none;
    font-family: "Arimo", sans-serif;
    font-size: 15px;
    color: var(--on-blue);
  }
  .contacts li {
    display: flex;
    align-items: center;
    gap: 12px;
    height: 26px;
  }
  .contacts svg { width: 14px; height: 14px; fill: var(--on-blue); }
  .web {
    position: absolute;
    right: 40px;
    bottom: 32px;
    margin: 0;
    font-family: "Arimo", sans-serif;
    font-weight: 700;
    font-size: 18px;
    letter-spacing: 1px;
    color: var(--on-blue);
  }
</style>
</head>
<body>
<main class="stage">

  <section class="card card--contact" aria-label="Card front, contact side">
    <svg class="bands" viewBox="0 0 700 420" aria-hidden="true">
      <path class="band-blue" d="M0,292 C240,262 480,205 700,168 L700,420 L0,420 Z"/>
      <path class="band-pink" d="M0,266 C240,236 470,182 660,150 C480,196 250,254 0,286 Z"/>
    </svg>

    <p class="company-name">PingRuiTang</p>

    <div class="person">
      <p class="person__name">Marcus Dole</p>
      <p class="person__title">Chairman</p>
    </div>

    <ul class="contacts">
      <li><svg viewBox="0 0 16 16"><path d="M3 1h3l1 4-2 1a9 9 0 0 0 5 5l1-2 4 1v3a2 2 0 0 1-2 2A13 13 0 0 1 1 3a2 2 0 0 1 2-2z"/></svg>0574-71948263</li>
      <li><svg viewBox="0 0 16 16"><rect x="4" y="0" width="8" height="16" rx="2"/></svg>13857420916</li>
      <li><svg viewBox="0 0 16 16"><path d="M0 3h16v10H0z M1 4l7 5 7-5"/></svg>kelvora@mailnest.example</li>
      <li><svg viewBox="0 0 16 16"><path d="M8 0a5 5 0 0 1 5 5c0 4-5 11-5 11S3 9 3 5a5 5 0 0 1 5-5zm0 3a2 2 0 1 0 0 4 2 2 0 0 0 0-4z"/></svg>No.258, LanpingJie, BeiyuanQu, Ningbo, Zhejiang</li>
    </ul>
  </section>

  <section class="card card--brand" aria-label="Card back, brand side">
    <svg class="bands" viewBox="0 0 700 420" aria-hidden="true">
      <path class="band-blue" d="M300,420 C460,358 590,300 700,262 L700,420 Z"/>
      <path class="band-pink" d="M300,398 C450,320 590,262 700,236 L700,254 C580,282 450,336 300,398 Z"/>
    </svg>

    <p class="company-name">PingRuiTang</p>

    <p class="web">www.prt2019.example</p>
  </section>

</main>
</body>
</html>
```